Upmarket Dessert Lounge needs a Business Card Design

We are an upmarket dessert lounge needing a business card to match our image.

We want something that is simple yet beautiful, feminine, classy, sophisticated and elegant. We want it to stand out and don't mind if it is bold.

The design should include our logo and colours of red or maroon with gold highlights. We don't mind if black is used.

Marlow & Quince

Target Market(s)

For those who like to indulge or treat themselves and give in to their temptations on good quality desserts.

Industry/Entity Type

Business

Requirements
Must have
• Must include our logo and our name

Marlow & Quince

M & Q

```html
<!DOCTYPE html>
<html lang="en">
<head>
<meta charset="utf-8">
<title>Marlow &amp; Quince — Business Card</title>
<link rel="stylesheet" href="https://fonts.googleapis.com/css2?family=Source+Sans+3:wght@400;600;700&display=swap">
<style>
  :root {
    --maroon: #7a1416;
    --maroon-deep: #6b1012;
    --cream: #f6cf98;
    --cream-soft: #f9e2c0;
    --paper: #ffffff;
    --ink: #3d3d3d;
    --backdrop: #efeae4;
  }
  * { box-sizing: border-box; margin: 0; padding: 0; }
  html, body {
    width: 1200px; height: 402px; overflow: hidden;
    background: var(--backdrop);
    font-family: "Source Sans 3", Arial, sans-serif;
  }
  .canvas { position: relative; width: 1200px; height: 402px; }
  .card {
    position: absolute; top: 56px;
    width: 510px; height: 290px; overflow: hidden;
    box-shadow: 0 2px 6px rgba(0,0,0,.18);
  }
  .card--front { left: 62px; background: var(--paper); }
  .card--back { left: 628px; background: var(--maroon); }

  .front-swoosh { position: absolute; inset: 0; }

  .brand-name {
    position: absolute; left: 0; right: 0; top: 44px;
    text-align: center; color: var(--maroon);
    font-weight: 600; font-size: 27px; letter-spacing: 1.5px;
    text-transform: uppercase;
  }

  .contact {
    position: absolute; top: 142px; left: 0; width: 510px;
    font-size: 13px; line-height: 19px; color: var(--ink);
  }
  .contact__address {
    position: absolute; right: 267px; top: 0; text-align: right;
  }
  .contact__divider {
    position: absolute; left: 256px; top: 2px; width: 1px; height: 56px;
    background: var(--maroon);
  }
  .contact__lines { position: absolute; left: 268px; top: 0; }
  .contact__row { display: flex; align-items: center; gap: 5px; white-space: nowrap; }
  .contact__row svg { width: 10px; height: 10px; flex: none; }
  .contact__address .contact__row { justify-content: flex-end; }

  .person {
    position: absolute; left: 287px; top: 252px;
    color: var(--paper); font-size: 20px; white-space: nowrap;
  }
  .person__name { font-weight: 700; }
  .person__title { font-weight: 400; font-size: 16px; }

  .monogram {
    position: absolute; inset: 0;
    display: flex; align-items: center; justify-content: center;
    color: var(--cream); font-weight: 600; font-size: 84px; letter-spacing: 2px;
  }
</style>
</head>
<body>
<main class="canvas">
  <section class="card card--front" aria-label="Business card front">
    <svg class="front-swoosh" viewBox="0 0 510 290" preserveAspectRatio="none" aria-hidden="true">
      <path fill="var(--maroon)" d="M0,128 C10,200 90,232 240,226 C160,238 40,230 0,200 Z"/>
      <path fill="var(--cream)" d="M0,188 C70,246 200,246 320,208 C410,180 470,210 510,282 L510,290 C470,222 410,196 320,222 C200,258 60,250 0,204 Z"/>
      <path fill="var(--maroon)" d="M0,210 C60,256 200,262 320,226 C410,200 470,226 510,290 L0,290 Z"/>
    </svg>

    <div class="brand-name">Marlow &amp; Quince</div>

    <div class="contact">
      <div class="contact__address">
        <div class="contact__row">Street Name, City Name</div>
        <div class="contact__row">State Zip Code</div>
        <div class="contact__row">
          <svg viewBox="0 0 10 10" aria-hidden="true"><circle cx="5" cy="5" r="4.3" fill="none" stroke="var(--maroon)" stroke-width="1.2"/><ellipse cx="5" cy="5" rx="1.8" ry="4.3" fill="none" stroke="var(--maroon)" stroke-width="1"/><line x1="0.7" y1="5" x2="9.3" y2="5" stroke="var(--maroon)" stroke-width="1"/></svg>
          www.marlowquince.com
        </div>
      </div>
      <div class="contact__divider"></div>
      <div class="contact__lines">
        <div class="contact__row">
          <svg viewBox="0 0 10 10" aria-hidden="true"><path fill="var(--maroon)" d="M2,0.5 L3.8,2.6 L2.8,3.8 C3.5,5.3 4.7,6.5 6.2,7.2 L7.4,6.2 L9.5,8 L8.2,9.5 C4.5,9.2 0.8,5.5 0.5,1.8 Z"/></svg>
          987-654-3210
        </div>
        <div class="contact__row">
          <svg viewBox="0 0 10 10" aria-hidden="true"><rect x="2.5" y="0.5" width="5" height="9" rx="1" fill="var(--maroon)"/><rect x="3.4" y="1.6" width="3.2" height="4.2" fill="var(--paper)"/></svg>
          987-654-3210
        </div>
        <div class="contact__row">
          <svg viewBox="0 0 10 10" aria-hidden="true"><rect x="0.5" y="2" width="9" height="6" fill="var(--maroon)"/><path d="M0.8,2.3 L5,5.4 L9.2,2.3" fill="none" stroke="var(--paper)" stroke-width="0.9"/></svg>
          info@marlowquince.com
        </div>
      </div>
    </div>

    <div class="person"><span class="person__name">Your name,</span> <span class="person__title">Title</span></div>
  </section>

  <section class="card card--back" aria-label="Business card back">
    <div class="monogram">M &amp; Q</div>
  </section>
</main>
</body>
</html>
```